Casino with the 'highest winning percentage' needs a stationery design

This is for a casino in Colombo, Sri Lanka and we need a stationery design for business card, letter head and envelope.

Should be very professional, simple and elegant without fancy fonts

Reason: Not fully satisfied with the designs. Need more designs.

Business

• 1. card deck symbol 'CLUBS' in red, or black

2. name in BLOCK CAPITAL LETTERS

3. Preferred font colours are black, white or red

4. Prefer 'professional /elegant' fonts
• SHOULD NOT HAVE ANY OTHER SYMBOL EXCEPT 'CLUBS'

DO NOT PREFER ITALIC FONTS

```html
<!DOCTYPE html>
<html lang="en">
<head>
<meta charset="utf-8">
<title>Halden's Entertainment – With Compliments Slip</title>
<link rel="stylesheet" href="https://fonts.googleapis.com/css2?family=Arimo:wght@400;700&display=swap">
<style>
  :root {
    --backdrop: #e9e9e9;
    --paper: #f4f4f3;
    --ink: #333333;
    --ink-soft: #4a4a4a;
    --brand-red: #a51d2a;
    --brand-red-light: #c97a80;
  }
  * { box-sizing: border-box; margin: 0; padding: 0; }
  html, body {
    width: 1200px;
    height: 620px;
    overflow: hidden;
    background: var(--backdrop);
    font-family: "Arimo", Arial, sans-serif;
    color: var(--ink);
  }
  .slip {
    position: absolute;
    left: 40px;
    top: 45px;
    width: 1120px;
    height: 529px;
    background: var(--paper);
    overflow: hidden;
  }
  .corner-decoration {
    position: absolute;
    right: 0;
    bottom: 0;
    width: 420px;
    height: 529px;
  }
  .brand {
    position: absolute;
    left: 76px;
    top: 68px;
    width: 194px;
    text-align: center;
    color: var(--ink-soft);
    font-weight: 400;
  }
  .brand-mark {
    display: block;
    width: 60px;
    height: 60px;
    margin: 0 auto 20px;
    border-radius: 50%;
    background: var(--brand-red);
  }
  .brand-name {
    font-size: 38px;
    line-height: 1;
    letter-spacing: 1px;
  }
  .brand-division {
    margin-top: 10px;
    font-size: 17px;
    letter-spacing: 0.5px;
    padding-bottom: 8px;
    border-bottom: 1px solid var(--ink-soft);
    width: 170px;
    margin-left: auto;
    margin-right: auto;
  }
  .brand-region {
    margin-top: 6px;
    font-size: 12px;
    letter-spacing: 1px;
  }
  .compliments {
    position: absolute;
    left: 76px;
    top: 410px;
  }
  .compliments-title {
    font-size: 36px;
    font-weight: 400;
    color: var(--ink);
    line-height: 1;
  }
  .compliments-title .accent { color: var(--brand-red); }
  .contact-address {
    margin-top: 18px;
    font-size: 13.5px;
    color: var(--ink-soft);
  }
  .contact-lines {
    margin-top: 7px;
    font-size: 13.5px;
    color: var(--ink-soft);
  }
  .contact-lines b { font-weight: 700; color: var(--ink); }
  .contact-sep {
    display: inline-block;
    width: 5px;
    height: 5px;
    margin: 0 8px 2px;
    border-radius: 50%;
    background: var(--brand-red);
  }
</style>
</head>
<body>
  <main class="slip">
    <svg class="corner-decoration" viewBox="0 0 420 529" aria-hidden="true">
      <defs>
        <linearGradient id="corner-fill" x1="0" y1="0" x2="0.4" y2="1">
          <stop offset="0" stop-color="#cf9ba0"/>
          <stop offset="0.45" stop-color="#a51d2a"/>
          <stop offset="1" stop-color="#9a1a26"/>
        </linearGradient>
      </defs>
      <circle cx="420" cy="529" r="400" fill="url(#corner-fill)"/>
    </svg>

    <header class="brand">
      <span class="brand-mark"></span>
      <div class="brand-name">HALDEN'S</div>
      <div class="brand-division">ENTERTAINMENT</div>
      <div class="brand-region">SRI LANKA</div>
    </header>

    <section class="compliments">
      <h1 class="compliments-title">With <span class="accent">Compliments</span></h1>
      <p class="contact-address">18, Lotus Garden Mawatha, Colombo 01000, Sri Lanka</p>
      <p class="contact-lines">
        <b>Tel:</b> + 94 11 2456780<span class="contact-sep"></span><b>Fax:</b> + 94 11 2456791<span class="contact-sep"></span>www.<b>haldenscolombo</b>.com
      </p>
    </section>
  </main>
</body>
</html>
```